Business Card Design Project

Looking to update our business cards. We have a logo with our slogan. We are an IT firm so we wouldlike a modern look.

Industry/Entity Type

Business

```html
<!DOCTYPE html>
<html lang="en">
<head>
<meta charset="utf-8">
<title>Kernova Business Card</title>
<link rel="stylesheet" href="https://fonts.googleapis.com/css2?family=Questrial&family=Arimo:wght@400;700&display=swap">
<style>
  :root {
    --stage: #3b3b3b;
    --yellow: #f7c300;
    --yellow-light: #ffd640;
    --olive: #a39b00;
    --olive-dark: #556400;
    --logo: #6f7b1a;
    --white: #ffffff;
    --ink: #222222;
  }
  html, body {
    margin: 0;
    padding: 0;
    width: 1200px;
    height: 1177px;
    overflow: hidden;
    background: var(--stage);
  }
  .canvas {
    width: 1200px;
    height: 1177px;
    display: flex;
    flex-direction: column;
    align-items: center;
    justify-content: center;
    gap: 50px;
  }
  .card {
    width: 900px;
    height: 514px;
    display: block;
    box-shadow: 0 6px 18px rgba(0,0,0,0.35);
  }
  .brand-name {
    font-family: "Questrial", sans-serif;
    fill: var(--logo);
    letter-spacing: 10px;
  }
  .brand-slogan {
    font-family: "Questrial", sans-serif;
    fill: var(--logo);
    letter-spacing: 3px;
  }
  .contact-name, .contact-line {
    font-family: "Arimo", sans-serif;
    fill: var(--ink);
  }
  .contact-name { font-weight: 700; font-size: 19px; }
  .contact-line { font-size: 16px; }
</style>
</head>
<body>
<main class="canvas">

  <!-- Contact side -->
  <svg class="card card-front" viewBox="0 0 900 514" xmlns="http://www.w3.org/2000/svg" aria-label="Business card, contact side">
    <defs>
      <linearGradient id="front-shade" x1="0" y1="0" x2="0" y2="1">
        <stop offset="0" stop-color="#cfcfcf"/>
        <stop offset="1" stop-color="#ffffff"/>
      </linearGradient>
    </defs>
    <rect class="field-yellow" width="900" height="514" fill="var(--yellow)"/>
    <path class="band-olive" d="M0,170 C220,250 420,90 900,70 L900,200 C460,210 250,360 0,330 Z" fill="var(--olive)"/>
    <path class="ribbon-dark" d="M0,215 C170,260 300,180 430,150 C320,200 200,290 0,265 Z" fill="var(--olive-dark)"/>
    <path class="band-edge" d="M0,322 C250,352 460,200 900,188 L900,204 C470,216 260,370 0,338 Z" fill="var(--white)"/>
    <path class="field-white" d="M0,338 C260,370 470,216 900,204 L900,514 L0,514 Z" fill="var(--white)"/>
    <path class="field-shade" d="M0,338 C260,370 470,216 900,204 L900,250 C500,260 280,400 0,380 Z" fill="url(#front-shade)" opacity="0.6"/>

    <g class="brand">
      <circle cx="70" cy="418" r="9" fill="var(--logo)"/>
      <text class="brand-name" x="90" y="430" font-size="36">KERNOVA</text>
      <text class="brand-slogan" x="58" y="458" font-size="13">MAKING TECH WORK FOR YOU</text>
    </g>

    <g class="contact">
      <text class="contact-name" x="490" y="300">Cardholder's Name</text>
      <text class="contact-name" x="490" y="322">Job Title</text>
      <text class="contact-line" x="490" y="376">9999, Address Line, Your City</text>
      <text class="contact-line" x="490" y="400">Tel : 00-11-222-3333</text>
      <text class="contact-line" x="490" y="424">Fax: 00-11-222-3333</text>
      <text class="contact-line" x="490" y="448">Email : hello@kernova.example</text>
      <text class="contact-line" x="490" y="472">Web : www.kernova.example</text>
    </g>
  </svg>

  <!-- Brand side -->
  <svg class="card card-back" viewBox="0 0 900 514" xmlns="http://www.w3.org/2000/svg" aria-label="Business card, brand side">
    <defs>
      <radialGradient id="map-glow" cx="0.5" cy="0.5" r="0.5">
        <stop offset="0" stop-color="var(--yellow-light)" stop-opacity="0.8"/>
        <stop offset="1" stop-color="var(--yellow)" stop-opacity="0"/>
      </radialGradient>
      <linearGradient id="back-shade" x1="0" y1="0" x2="0" y2="1">
        <stop offset="0" stop-color="#c8c8c8"/>
        <stop offset="1" stop-color="#ffffff"/>
      </linearGradient>
    </defs>
    <rect class="field-yellow" width="900" height="514" fill="var(--yellow)"/>
    <rect class="map-decoration" x="380" y="20" width="500" height="280" fill="url(#map-glow)" role="img" aria-label="Faint world map with hexagon and circuit pattern"/>

    <g class="brand">
      <circle cx="450" cy="170" r="12" fill="var(--logo)"/>
      <text class="brand-name" x="476" y="186" font-size="52">KERNOVA</text>
      <text class="brand-slogan" x="446" y="226" font-size="19">MAKING TECH WORK FOR YOU</text>
    </g>

    <path class="band-olive" d="M0,280 C200,250 420,300 560,360 C700,420 820,440 900,440 L900,514 L0,514 Z" fill="var(--olive)"/>
    <path class="ribbon-dark" d="M60,285 C220,280 320,320 400,380 L420,420 C330,350 220,310 60,295 Z" fill="var(--olive-dark)"/>
    <path class="band-edge" d="M0,300 C200,290 380,350 520,420 C620,470 700,500 760,514 L0,514 Z" fill="var(--white)"/>
    <path class="field-white" d="M0,312 C200,302 370,360 505,430 C590,475 650,500 700,514 L0,514 Z" fill="var(--white)"/>
    <path class="field-shade" d="M0,312 C200,302 370,360 505,430 C590,475 650,500 700,514 L620,514 C520,470 340,360 0,345 Z" fill="url(#back-shade)" opacity="0.55"/>
  </svg>

</main>
</body>
</html>
```